Web design for financial services

A modern web design of financial services (brokerage firm)
Req.s and technology tags :
- Very mobile friendly.
- One paged with some inner pages.
- Animated sticky header .
- Member login area for e-trade.
- Support RTL language.
- HTML & CSS.

The logo will be Home link
• MPTR :
WHO WE ARE
Content :
i) Board of Directors
ii) Mission Statement
iii) Corporate Values
iv) Regulations
• Financial Services :
WHAT WE DO
Content:
i) Electronic trading
ii) Trading desk
iii) Institutional
iv) Investors Education
• News
• Market Tools
• Forms---- opens new page
• Careers---- opens new page
• Contact Us----opens new page

The website is :
http://www.mptr-doha-example.com/

The logo need some changes to be more modern and impressively , but with keeping same structure .

Some related websites :
https://www.lv-bourse.example/

financial market

Financial Service

Coded - Design and coding required

2 page

• same fonts of http://www.kwdholdings.example/

• - Very mobile friendly.
• - One paged with some inner pages.
• - Animated sticky header .
• - Member login area for e-trade.
• - Support RTL language.
• - HTML & CSS.
• Slider , some Qatari theme,
• i like the video inside the home page
• ex :http://www.kwdholdings.example/

```html
<!DOCTYPE html>
<html lang="en">
<head>
<meta charset="utf-8">
<title>MPTR — Financial Services</title>
<link href="https://fonts.googleapis.com/css2?family=Open+Sans:ital,wght@0,400;0,600;0,700;0,800;1,400&display=swap" rel="stylesheet">
<style>
  :root{
    --brand-red:#8f1f1f;
    --brand-red-dark:#7a1a1a;
    --ink:#1d1d1d;
    --text:#333333;
    --muted:#555555;
    --rule:#d6d6d6;
    --white:#ffffff;
    --footer-bg:#000000;
    --hero-dark:#2b2f36;
    --hero-warm:#5a3b2c;
    --skyline-light:#d6a5a0;
    --skyline-mid:#b5655e;
    --skyline-deep:#8a3a35;
  }
  *{box-sizing:border-box;margin:0;padding:0}
  html,body{width:1200px;height:2273px;overflow:hidden}
  body{position:relative;background:var(--white);font-family:"Open Sans",Arial,sans-serif;color:var(--text)}

  /* Header */
  .site-header{position:absolute;left:0;top:0;width:1200px;height:121px;background:var(--white)}
  .brand{position:absolute;left:76px;top:38px;display:flex;align-items:center;gap:12px;text-decoration:none}
  .brand-mark{width:40px;height:40px;background:var(--brand-red)}
  .brand-name{font-size:40px;font-weight:800;color:var(--ink);letter-spacing:1px;line-height:1}
  .utility-bar{position:absolute;top:27px;right:76px;display:flex;gap:9px}
  .btn-etrade{height:26px;padding:0 10px;background:var(--brand-red);color:var(--white);font-size:10px;font-weight:700;display:flex;align-items:center;gap:6px;border-radius:2px}
  .btn-etrade svg{width:11px;height:11px}
  .lang-select{height:26px;width:88px;border:1px solid #999;border-radius:2px;font-size:9px;font-weight:600;color:var(--ink);display:flex;align-items:center;gap:5px;padding-left:7px}
  .lang-flag{width:13px;height:9px;background:#2c3e7a;border:1px solid #c9c9c9}
  .main-nav{position:absolute;top:80px;right:76px;display:flex;gap:36px}
  .main-nav a{font-size:12px;font-weight:700;color:var(--ink);text-decoration:none}
  .main-nav a.is-active{color:var(--brand-red)}

  /* Hero */
  .hero{position:absolute;left:0;top:121px;width:1200px;height:546px;background:linear-gradient(115deg,var(--hero-dark) 0%,#4a4a4f 40%,var(--hero-warm) 70%,#1e2228 100%)}
  .hero-title{position:absolute;left:0;right:0;top:180px;text-align:center;font-size:62px;font-weight:700;color:var(--white);letter-spacing:1px}
  .hero-cut{position:absolute;left:0;top:121px;width:1200px;height:546px}

  /* Content */
  .side-nav{position:absolute;left:161px;top:700px;width:170px}
  .side-nav-title{font-size:14px;font-weight:700;color:var(--brand-red)}
  .side-nav-rule{width:45px;height:4px;background:var(--ink);margin:13px 0 18px}
  .side-nav ul{list-style:none}
  .side-nav li{font-size:11.5px;font-weight:700;color:var(--ink);height:34.8px}
  .divider{position:absolute;left:341px;top:700px;width:1px;height:903px;background:var(--rule)}

  .article{position:absolute;left:380px;width:662px}
  .article h2{font-size:20px;font-weight:700;color:var(--brand-red)}
  .lead{font-size:13.5px;font-style:italic;line-height:25px;color:var(--text);margin-top:20px}
  .body-copy{font-size:10.8px;line-height:21px;color:var(--text)}
  .intro{top:697px}
  .intro .body-copy{margin-top:18px}

  .features{position:absolute;left:380px;top:975px;list-style:none}
  .features li{position:relative;padding-left:20px;font-size:10.8px;color:var(--ink);height:27px;line-height:16px}
  .features li::before{content:"";position:absolute;left:2px;top:4px;width:7px;height:7px;background:var(--brand-red);transform:rotate(45deg)}
  .feature-art{position:absolute;left:659px;top:936px;width:380px;height:215px;border-radius:4px;background:linear-gradient(135deg,#e3e8f0 0%,#cdd6e2 55%,#b9c3cf 100%)}

  .section-two{top:1216px}
  .section-three{top:1431px}
  .section-two .body-copy,.section-three .body-copy{margin-top:15px}

  /* Skyline + footer */
  .skyline{position:absolute;left:0;top:1689px;width:1200px;height:329px;background:linear-gradient(180deg,var(--white) 0%,var(--skyline-light) 35%,var(--skyline-mid) 70%,var(--skyline-deep) 100%)}
  .site-footer{position:absolute;left:0;top:2018px;width:1200px;height:255px;background:var(--footer-bg);color:var(--white);text-align:center}
  .footer-brand{position:absolute;left:0;right:0;top:58px;display:flex;justify-content:center;align-items:center;gap:9px}
  .footer-brand .brand-mark{width:30px;height:30px;border-radius:50%;background:var(--white)}
  .footer-brand .brand-name{font-size:28px;color:var(--white)}
  .footer-nav{position:absolute;left:0;right:0;top:126px;font-size:13px;font-weight:700}
  .footer-nav span.sep{margin:0 14px}
  .legal{position:absolute;left:0;right:0;top:160px;font-size:10px}
  .social{position:absolute;left:0;right:0;top:191px;display:flex;justify-content:center;gap:8px}
  .social span{width:30px;height:30px;border:1.5px solid var(--white);border-radius:50%}
</style>
</head>
<body>

<header class="site-header">
  <a class="brand" href="#"><span class="brand-mark"></span><span class="brand-name">MPTR</span></a>
  <div class="utility-bar">
    <div class="btn-etrade">
      <svg viewBox="0 0 12 12"><rect x="1" y="1" width="7" height="10" fill="none" stroke="#fff" stroke-width="1.2"/><path d="M5 6h6M9 4l2 2-2 2" fill="none" stroke="#fff" stroke-width="1.2"/></svg>
      MPTR E-TRADE
    </div>
    <div class="lang-select"><span class="lang-flag"></span>ENGLISH
      <svg width="7" height="5" viewBox="0 0 7 5"><path d="M1 1l2.5 2.5L6 1" fill="none" stroke="#333" stroke-width="1.2"/></svg>
    </div>
  </div>
  <nav class="main-nav">
    <a class="is-active" href="#">MPTR</a>
    <a href="#">FINANCIAL SERVICE</a>
    <a href="#">NEWS</a>
    <a href="#">MARKET TOOL</a>
    <a href="#">FORMS</a>
    <a href="#">CAREERS</a>
    <a href="#">CONTACT US</a>
  </nav>
</header>

<section class="hero" role="img" aria-label="Photograph of a trader at a laptop reviewing printed financial charts">
  <h1 class="hero-title">FINANCIAL SERVICES</h1>
</section>
<svg class="hero-cut" viewBox="0 0 1200 546" aria-hidden="true"><polygon points="0,470 371,399 1200,546 0,546" fill="#fff"/></svg>

<aside class="side-nav">
  <div class="side-nav-title">FINANCIAL SERVICES</div>
  <div class="side-nav-rule"></div>
  <ul>
    <li>ELECTRONIC TRADING</li>
    <li>TRADING DESK</li>
    <li>MOBILE APPLICATION</li>
    <li>INSTITUTIONAL</li>
    <li>INVESTOR EDUCATION</li>
  </ul>
</aside>
<div class="divider"></div>

<article class="article intro">
  <h2>Sed ut perspiciatis unde omnisna voluptatem</h2>
  <p class="lead">Sed ut perspiciatis unde omnis iste natus error sit voluptatem accusantium doloremque laudantium, totam rem aperiam, eaque ipsa quae ab illo inventore veritatis et quasi architecto beatae vitae dicta suaque ipsa quae ab illo inventore ve ipsa quae ab illo inventoreritatis.</p>
  <p class="body-copy">Sed ut perspiciatis unde omnis iste natus error sit voluptatem accusantium dolore mque laudantium, totam remape riam, eaque ipsa quae ab illo inventore veritatis et quasi arc hite cto beatae vitae dictasnt explic abo enim ilorepsam vol uptatemloia voluptas sit aspe rnatur aut odit auhite cto bea tae vitae dictasnt explic abo enim ilorepsam vol uptateloia voluptas sit aspe rnatur aut odit auhite cto beatae vitae dictst explic abo enim ilorepsam vol uptatemloia voluptas sit aspe rnatur aut odit auhite cto bea tae</p>
</article>

<ul class="features">
  <li>Lorem ipsum dolor situr adipiscing elit.</li>
  <li>Sed varius est quis quam auctor, isto cursus.</li>
  <li>Donec et maitur rhonus, interdum nislitudin ex.</li>
  <li>Curabitur rhoncus nisi in urlamcorper faucibus.</li>
  <li>Curabitur vitae quam nec sem ullamcisus.</li>
  <li>Durabitur rhoncus nisi in urlamcorper faucibus.</li>
  <li>Hurabitur vitae quam nec sem ullamcisus.</li>
</ul>
<div class="feature-art" role="img" aria-label="Illustration of laptop, monitor, tablet and phone showing market charts under clouds"></div>

<article class="article section-two">
  <h2>Sed ut perspiciatis unde omnisna voluptatem</h2>
  <p class="body-copy">Sed ut perspiciatis unde omnis iste natus error sit voluptat em accusantium dolore mque laudantium, totam remape riam, eaque ipsa quae ab illo inventore veritatis et quasi arc hite cto beatae vitae dictasnt explic abo enim ilorepsam vol uptat emloia voluptas sit aspe rnatur aut odit auhite cto bea tae vitae dictasnt explic abo enim ilorepsam vol uptateloia voluptas sit aspe rnatur aut odiatur aut odit auhite cto bea tae vitae dictasnt explic abo enimt au. eaque ipsa quae ab illo inventore veritatis et quasi arc hite cto beatae vitae dictasnt explic abo enim ilorepsam vol uptat emloia voluptas sit aspe rnatur aut odit auhite cto bea tae vitae dictasnt explic abo enim ilorepsam vol uptateloia voluptas s.</p>
</article>

<article class="article section-three">
  <h2>Sed ut perspiciatis unde omnisna voluptatem</h2>
  <p class="body-copy">Sed ut perspiciatis unde omnis iste natus error sit voluptat em accusantium dolore mque laudantium, totam remape riam, eaque ipsa quae ab illo inventore veritatis et quasi arc hite cto beatae vitae dictasnt explic abo enim ilorepsam vol uptat emloia voluptas sit aspe rnatur aut odit auhite cto bea tae vitae dictasnt explic abo enim ilorepsam vol uptateloia voluptas sit aspe rnatur aut odiatur aut odit auhite cto bea tae vitae dictasnt explic abo enimt au. eaque ipsa quae ab illo inventore veritatis et quasi arc hite cto beatae vitae dictasnt explic abo enim ilorepsam vol uptat emloia voluptas sit aspe rnatur aut odit auhite cto bea tae vitae dictasnt explic abo enim ilorepsam vol uptateloia voluptas s.</p>
</article>

<div class="skyline" role="img" aria-label="Illustrated Doha city skyline in shades of muted red"></div>

<footer class="site-footer">
  <div class="footer-brand"><span class="brand-mark"></span><span class="brand-name">MPTR</span></div>
  <nav class="footer-nav">MPTR<span class="sep">|</span>FINACIAL SERVICE<span class="sep">|</span>NEWS<span class="sep">|</span>MARKET TOOL<span class="sep">|</span>CAREERS<span class="sep">|</span>CONTACT US</nav>
  <p class="legal">©2017. All Rights Reserved | MPTR Qatar | Copyright, Legal and Privacy Statement.Disclaimers and Legal Information</p>
  <div class="social" aria-label="Social links"><span></span><span></span><span></span><span></span><span></span></div>
</footer>

</body>
</html>
```